Upmarket Dessert Lounge needs a Business Card Design

We are an upmarket dessert lounge needing a business card to match our image.

We want something that is simple yet beautiful, feminine, classy, sophisticated and elegant. We want it to stand out and don't mind if it is bold.

The design should include our logo and colours of red or maroon with gold highlights. We don't mind if black is used.

Marlow & Quince

Target Market(s)

For those who like to indulge or treat themselves and give in to their temptations on good quality desserts.

Industry/Entity Type

Business

Requirements
Must have
• Must include our logo and our name

Marlow & Quince

M & Q

```html
<!DOCTYPE html>
<html lang="en">
<head>
<meta charset="utf-8">
<title>Marlow &amp; Quince — Business Card</title>
<link rel="stylesheet" href="https://fonts.googleapis.com/css2?family=Libre+Baskerville:wght@400&family=Noto+Sans:wght@400&display=swap">
<style>
  :root {
    --backdrop: #e4e2df;
    --maroon: #8e1a1c;
    --maroon-deep: #5e0d10;
    --maroon-light: #a8282a;
    --gold: #e7c28f;
    --gold-soft: #d9a96c;
    --gold-glow: rgba(217,169,108,0.5);
    --gold-glow-faint: rgba(217,169,108,0.18);
    --gold-clear: rgba(217,169,108,0);
    --cream: #f6cd98;
    --band: #241815;
    --ink: #2a1a17;
    --white: #ffffff;
  }
  * { margin: 0; padding: 0; box-sizing: border-box; }
  html, body { width: 1200px; height: 951px; overflow: hidden; }
  body {
    background: var(--backdrop);
    position: relative;
    font-family: "Noto Sans", Verdana, sans-serif;
  }
  .card {
    position: absolute;
    width: 620px;
    height: 355px;
    border-radius: 22px;
    overflow: hidden;
    box-shadow: 0 10px 28px rgba(0,0,0,0.25);
  }
  /* Front */
  .card--front {
    left: 90px; top: 100px;
    background: radial-gradient(ellipse at 40% 40%, var(--maroon-light) 0%, var(--maroon) 45%, var(--maroon-deep) 100%);
  }
  .front__ornament {
    position: absolute;
    right: -40px; top: -70px;
    width: 380px; height: 230px;
    background: radial-gradient(closest-side, var(--gold-glow) 0%, var(--gold-glow-faint) 55%, var(--gold-clear) 100%);
  }
  .front__name {
    position: absolute;
    left: 0; width: 460px; top: 120px;
    text-align: center;
    font-family: "Libre Baskerville", Georgia, serif;
    font-size: 34px;
    letter-spacing: 1px;
    color: var(--gold);
  }
  .front__web {
    position: absolute;
    left: 0; width: 460px; top: 262px;
    text-align: center;
    font-family: "Libre Baskerville", Georgia, serif;
    font-size: 15px;
    letter-spacing: 0.5px;
    color: var(--white);
  }
  /* Back */
  .card--back {
    left: 490px; top: 490px;
    background: var(--cream);
  }
  .back__shape { position: absolute; inset: 0; }
  .back__name {
    position: absolute;
    left: 40px; top: 40px;
    width: 300px;
    text-align: center;
    font-family: "Libre Baskerville", Georgia, serif;
    font-size: 26px;
    color: var(--maroon);
  }
  .contact {
    position: absolute;
    left: 30px; top: 200px;
    list-style: none;
    font-size: 15px;
    color: var(--ink);
  }
  .contact li {
    display: flex; align-items: center; gap: 10px;
    height: 24px;
  }
  .contact svg { width: 14px; height: 14px; flex: none; }
  .back__title {
    position: absolute;
    right: 34px; bottom: 58px;
    font-size: 21px;
    color: var(--white);
  }
  .back__title .amp { color: var(--gold-soft); }
</style>
</head>
<body>
  <section class="card card--front">
    <div class="front__ornament" role="img" aria-label="Gold floral flourish in the top-right corner"></div>
    <div class="front__name">Marlow &amp; Quince</div>
    <div class="front__web">www.marlowquince.com</div>
  </section>

  <section class="card card--back">
    <svg class="back__shape" viewBox="0 0 620 355" preserveAspectRatio="none" aria-hidden="true">
      <defs>
        <radialGradient id="backRed" cx="70%" cy="50%" r="70%">
          <stop offset="0%" stop-color="#a8282a"/>
          <stop offset="100%" stop-color="#6a1013"/>
        </radialGradient>
      </defs>
      <path d="M360,0 C300,110 410,210 330,355 L620,355 L620,0 Z" fill="#241815"/>
      <path d="M400,0 C340,110 450,210 370,355 L620,355 L620,0 Z" fill="url(#backRed)"/>
    </svg>
    <div class="back__name">Marlow &amp; Quince</div>
    <ul class="contact">
      <li><svg viewBox="0 0 14 14"><circle cx="7" cy="7" r="6" fill="none" stroke="#5e0d10" stroke-width="1.5"/><path d="M4.5 4 L6 4 L6.5 6 L5.6 6.7 Q6.5 8.5 8 9 L8.8 8 L10 8.6 L10 10 Q6 10.5 4.5 4Z" fill="#5e0d10"/></svg>555-014-2200</li>
      <li><svg viewBox="0 0 14 14"><rect x="4" y="1.5" width="6" height="11" rx="1.2" fill="#5e0d10"/><rect x="5" y="3" width="4" height="6" fill="#f6cd98"/></svg>555-014-2201</li>
      <li><svg viewBox="0 0 14 14"><rect x="1" y="3" width="12" height="8" rx="1" fill="#5e0d10"/><path d="M1.5 3.5 L7 8 L12.5 3.5" fill="none" stroke="#f6cd98" stroke-width="1"/></svg>info@marlowquince.com</li>
      <li><svg viewBox="0 0 14 14"><circle cx="7" cy="7" r="6" fill="#5e0d10"/></svg>www.marlowquince.com</li>
    </ul>
    <div class="back__title">Marlow <span class="amp">&amp;</span> Quince</div>
  </section>
</body>
</html>
```